Marwick Family Chiropractic Stationary

The letterhead and business card must have our logo.
We would like to see the logo used in different ways ( It can be expanded upon in the stationary.)
Please use the the same or similar colors.
Must be eye catching and memorable.
Must be easy to read

Reason: The doctor has been too busy to make any final decisions. He would like to give himself a little more time.

Target Market(s)

Chiropractic Healthcare

Industry/Entity Type

Business

Requirements
Must have
• Dr. Leonard Marwick D.C.
Chiropractor

860-555-0183

417 Birchfield Road, 2nd Floor
Fernhollow, Oakshire 06091

drmarwick@marwickspine.example
www.marwickspine.example
www.facebook.com/MarwickFamilySpine
Should not have
• should not be difficult to read

```html
<!DOCTYPE html>
<html lang="en">
<head>
<meta charset="utf-8">
<title>Marwick Family Chiropractic – Business Card Set</title>
<link rel="stylesheet" href="https://fonts.googleapis.com/css2?family=Montserrat:wght@700&family=Open+Sans:ital,wght@0,400;0,600;0,700;1,600;1,700&display=swap">
<style>
  :root {
    --backdrop: #8c5b37;
    --label: #2a1a10;
    --card-white: #ffffff;
    --card-espresso: #221a14;
    --card-black: #0a0a0a;
    --brand-green: #2d9a48;
    --leaf-green: #9cc45a;
    --bark: #2b1d15;
    --taupe: #9a8f82;
    --ink: #333333;
    --on-dark: #ffffff;
  }
  * { margin: 0; padding: 0; box-sizing: border-box; }
  html, body { width: 1200px; height: 788px; overflow: hidden; }
  body {
    background: var(--backdrop);
    font-family: "Open Sans", Arial, sans-serif;
    position: relative;
  }
  .view-label {
    position: absolute;
    font-size: 21px;
    color: var(--label);
    width: 525px;
    text-align: center;
  }
  .card {
    position: absolute;
    width: 525px;
    height: 300px;
    border-radius: 22px;
    overflow: hidden;
    box-shadow: 0 6px 14px rgba(0,0,0,.35);
  }
  .card--white { background: var(--card-white); }
  .card--espresso { background: var(--card-espresso); }
  .card--black { background: var(--card-black); }

  .corner-swoosh { position: absolute; inset: 0; }

  .brand {
    position: absolute;
    left: 0; right: 0;
    text-align: center;
    font-family: "Montserrat", Arial, sans-serif;
    font-weight: 700;
    line-height: 1;
  }
  .brand-mark {
    display: block;
    margin: 0 auto;
    border-radius: 50%;
  }
  .brand-name { display: block; color: var(--brand-green); }
  .brand-tagline { display: block; color: var(--bark); }

  .doctor-line {
    position: absolute;
    top: 183px; left: 0; right: 0;
    text-align: center;
    font-size: 14px;
    font-weight: 700;
    color: var(--brand-green);
  }
  .doctor-line .role { color: var(--ink); font-size: 12px; }
  .contact {
    position: absolute;
    top: 212px; left: 0; right: 0;
    text-align: center;
    font-size: 12.5px;
    color: var(--ink);
    line-height: 20.5px;
  }
  .contact .key { font-style: italic; font-weight: 700; }
  .web {
    position: absolute;
    left: 0; right: 0;
    bottom: 22px;
    text-align: center;
    font-size: 15px;
  }
</style>
</head>
<body>

  <div class="view-label" style="left:55px; top:34px;">Front</div>
  <div class="view-label" style="left:622px; top:34px;">Back - 1</div>
  <div class="view-label" style="left:54px; top:404px;">Back - 2</div>
  <div class="view-label" style="left:622px; top:404px;">Back - 3</div>

  <section class="card card--white" style="left:55px; top:77px;">
    <svg class="corner-swoosh" width="525" height="300" viewBox="0 0 525 300" aria-hidden="true">
      <path d="M455 0 Q505 18 525 62 L525 0 Z" fill="var(--brand-green)"/>
      <path d="M448 0 Q500 16 525 70" fill="none" stroke="var(--bark)" stroke-width="3"/>
      <path d="M0 222 Q20 278 80 300 L0 300 Z" fill="var(--brand-green)"/>
      <path d="M0 214 Q18 280 90 300" fill="none" stroke="var(--bark)" stroke-width="3"/>
    </svg>
    <div class="brand" style="top:22px;">
      <span class="brand-mark" style="width:74px; height:74px; background:var(--leaf-green);"></span>
      <span class="brand-name" style="font-size:24px; margin-top:30px;">MARWICK</span>
      <span class="brand-tagline" style="font-size:10px; margin-top:4px;">FAMILY CHIROPRACTIC</span>
    </div>
    <p class="doctor-line">Dr. Leonard Marwick D.C., <span class="role">Chiropractor</span></p>
    <div class="contact">
      <p><span class="key">phone</span> 860-555-0183 &nbsp;|&nbsp; <span class="key">email</span> mymarwick@marwickspine.example</p>
      <p><span class="key">web</span> : www.marwickspine.example &nbsp;|&nbsp; <span class="key">face book</span> : MarwickFamilySpine</p>
      <p>417 Birchfield Road, 2nd Floor, Fernhollow, Oakshire 06091</p>
    </div>
  </section>

  <section class="card card--white" style="left:622px; top:74px;">
    <div class="brand" style="top:32px;">
      <span class="brand-mark" style="width:112px; height:112px; background:var(--leaf-green);"></span>
      <span class="brand-name" style="font-size:33px; margin-top:24px;">MARWICK</span>
      <span class="brand-tagline" style="font-size:13px; margin-top:6px;">FAMILY CHIROPRACTIC</span>
    </div>
    <p class="web" style="color:var(--ink);">www.marwickspine.example</p>
  </section>

  <section class="card card--espresso" style="left:54px; top:445px;">
    <div class="brand" style="top:100px;">
      <span class="brand-name" style="font-size:62px;">MARWICK</span>
      <span class="brand-tagline" style="font-size:24px; margin-top:12px; color:var(--on-dark);">FAMILY CHIROPRACTIC</span>
    </div>
    <p class="web" style="color:var(--on-dark);">www.marwickspine.example</p>
  </section>

  <section class="card card--black" style="left:622px; top:445px;">
    <div class="brand" style="top:30px;">
      <span class="brand-mark" style="width:122px; height:122px; background:var(--brand-green);"></span>
      <span class="brand-name" style="font-size:30px; margin-top:22px; color:var(--leaf-green);">MARWICK</span>
      <span class="brand-tagline" style="font-size:12.5px; margin-top:6px; color:var(--taupe);">FAMILY CHIROPRACTIC</span>
    </div>
    <p class="web" style="color:var(--on-dark);">www.marwickspine.example</p>
  </section>

</body>
</html>
```